Meridale Bed Company Needs Business Card

Looking for a very nice looking business card. Creative but not extravagant. We sell beds and pillows across the U.S. and need something professional but catchy. I have attached the logo.

Name : Devin Holt
Title : President
Phone : (800) 471-2960
Email: sleep@quilmora.com
Website: www.quilmora.com

Can be single-sided or double-sided
horizontal or vertical

Can use Blues/Greys

Target Market(s)

Mass Market

Industry/Entity Type

Retail

Contact Information for Business Card

Name : Devin Holt
Title : President
Phone : (800) 471-2960
Email: sleep@quilmora.com
Website: www.quilmora.com

Requirements
Must have
• Clean, Modern, Smooth
• Can use Blues/Greys
• On the other side without the information - have something simple like www.quilmora.com or our logo
Nice to have
• Surprise me
Should not have
• Nothing crazy, nothing cluttered

```html
<!DOCTYPE html>
<html lang="en">
<head>
<meta charset="utf-8">
<title>Meridale Bed Company – Business Card</title>
<link href="https://fonts.googleapis.com/css2?family=Roboto:wght@300;400;700&display=swap" rel="stylesheet">
<style>
  :root {
    --backdrop: #e9ebee;
    --brand-blue: #35a2d4;
    --card-white: #ffffff;
    --text-grey: #555a5f;
    --rule-grey: #d2d4d6;
  }
  * { margin: 0; padding: 0; box-sizing: border-box; }
  html, body {
    width: 1200px;
    height: 1000px;
    overflow: hidden;
    background: var(--backdrop);
    font-family: "Roboto", Arial, sans-serif;
  }
  .canvas { position: relative; width: 1200px; height: 1000px; }

  .card {
    position: absolute;
    left: 243px;
    width: 709px;
    height: 405px;
  }

  /* Front side */
  .card-front {
    top: 84px;
    background: var(--brand-blue);
    color: var(--card-white);
  }
  .card-front .wordmark {
    position: absolute;
    left: 0; right: 0;
    top: 188px;
    text-align: center;
    font-weight: 300;
    font-size: 118px;
    line-height: 1;
    letter-spacing: 1px;
  }
  .card-front .web {
    position: absolute;
    left: 0; right: 0;
    top: 359px;
    text-align: center;
    font-size: 15px;
    font-weight: 400;
    letter-spacing: 0.3px;
  }

  /* Back side */
  .card-back {
    top: 526px;
    background: var(--card-white);
  }
  .card-back .side-rule {
    position: absolute;
    left: 69px;
    top: 0;
    width: 2px;
    height: 100%;
    background: var(--rule-grey);
  }
  .card-back .wordmark {
    position: absolute;
    left: 92px;
    top: 38px;
    font-weight: 300;
    font-size: 60px;
    line-height: 1;
    color: var(--brand-blue);
  }
  .person { position: absolute; left: 93px; top: 201px; }
  .person .name {
    font-size: 19px;
    font-weight: 700;
    color: var(--brand-blue);
    letter-spacing: 0.3px;
    line-height: 22px;
  }
  .person .title {
    font-size: 16px;
    color: var(--text-grey);
    line-height: 22px;
  }
  .contacts { position: absolute; left: 59px; top: 264px; list-style: none; }
  .contacts li {
    display: flex;
    align-items: center;
    height: 25.5px;
    font-size: 16px;
    color: var(--text-grey);
  }
  .contacts .icon { width: 21px; height: 21px; margin-right: 13px; flex: none; }
</style>
</head>
<body>
<main class="canvas">
  <section class="card card-front">
    <div class="wordmark">quilmora</div>
    <div class="web">www.quilmora.com</div>
  </section>

  <section class="card card-back">
    <div class="side-rule"></div>
    <div class="wordmark">quilmora</div>
    <div class="person">
      <div class="name">DEVIN HOLT</div>
      <div class="title">President</div>
    </div>
    <ul class="contacts">
      <li>
        <svg class="icon" viewBox="0 0 20 20" aria-hidden="true">
          <circle cx="10" cy="10" r="10" fill="var(--brand-blue)"/>
          <path d="M7 5.2c.4-.3.9-.2 1.1.2l.9 1.7c.2.4.1.8-.2 1.1l-.6.5c.5 1.1 1.3 2 2.4 2.6l.5-.6c.3-.3.7-.4 1.1-.2l1.7.9c.4.2.5.7.2 1.1l-.6.8c-.4.5-1.1.7-1.7.5-2.6-.9-4.5-2.9-5.3-5.5-.2-.6 0-1.3.5-1.7z" fill="#fff"/>
        </svg>
        (800) 471-2960
      </li>
      <li>
        <svg class="icon" viewBox="0 0 20 20" aria-hidden="true">
          <circle cx="10" cy="10" r="10" fill="var(--brand-blue)"/>
          <rect x="5" y="6.5" width="10" height="7" rx="0.8" fill="#fff"/>
          <path d="M5.3 7l4.7 3.6L14.7 7" fill="none" stroke="var(--brand-blue)" stroke-width="1"/>
        </svg>
        sleep@quilmora.com
      </li>
      <li>
        <svg class="icon" viewBox="0 0 20 20" aria-hidden="true">
          <circle cx="10" cy="10" r="10" fill="var(--brand-blue)"/>
          <g fill="none" stroke="#fff" stroke-width="1">
            <circle cx="10" cy="10" r="5"/>
            <ellipse cx="10" cy="10" rx="2.2" ry="5"/>
            <path d="M5 10h10M5.8 7.5h8.4M5.8 12.5h8.4"/>
          </g>
        </svg>
        www.quilmora.com
      </li>
    </ul>
  </section>
</main>
</body>
</html>
```